wardrobe/costume stylist needs good business card for own business

Hi:)

I'm wanting a business card for my company. I am a freelance stylist.

I do wardrobe/costume stylist to TV commercials; Films; Fashion and Lifestyle shoots.

I'd like a design based around my name Rosalind Parfrey written nicely, maybe a colour? Up to you?!

I've attached a couple of images of business cards I like
.... be creative and have fun!

Thank you :)

Reason: I was trying to get my new business card ready for before I headed overseas Friday morning but I don't think that was realistic so I'd like to extend the deadline to give time to the project. Thank you

Hi designers:) Thank you for all your designs, I've extended the deadline until Sunday, so there's a bit more time. I've attached 3 pictures of business cards which I quite like, please take a look to see if it can be of help in your process. I like the pale plain or patterned background with dark font and the dark plain or patterned background with the pale font the motifs the feminine fonts the plain fonts I like the idea of playing with a circle or some shape on one side of the card with my name or initials as in the picture I have on my post could you play around with this idea a bit please? Thank you all for the work you've done :) Rosa

Hi I am working overseas til Saturday night sorry for no feedback until I teturn Thanks :) Rosa

Hi designers, Thank you all so much for submitting your designs, I really appreciate your input into my project :) I'm sorry I didn't get to respond to some comments, and give feedback. I didn't back from being away until later than I expected, and the deadline had passed then, so apologies. Thanks to you all again for all your really good designs :) Rosa

Target Market(s)

I am a freelance stylist my target audience is producers, production companies, photographers, directors...

Industry/Entity Type

Business

Requirements
Must have
• Rosalind Parfrey
Stylist or Wardrobe Stylist

email rosaparfrey@mailbox-example.co.nz
Mobile 0218467193

(Don't have to use the words 'email' and 'mobile')
Nice to have
• Would like it to be double sided
Like B & W
Like pale colour background with dark font or white font
Like dark colour background with pale font
Should not have
• I would prefer it not to incorporate pictures

```html
<!DOCTYPE html>
<html lang="en">
<head>
<meta charset="utf-8">
<title>Rosalind Parfrey — Business Card</title>
<link rel="stylesheet" href="https://fonts.googleapis.com/css2?family=Pinyon+Script&family=Open+Sans:ital,wght@1,400;1,600&display=swap">
<style>
  :root {
    --backdrop: #a9a9a9;
    --card-black: #1a1a1a;
    --card-gold: #cb8d2a;
    --ink-white: #ffffff;
    --ink-dark: #1f1a14;
  }
  html, body {
    margin: 0;
    padding: 0;
    overflow: hidden;
  }
  .canvas {
    position: relative;
    width: 1200px;
    height: 655px;
    background: var(--backdrop);
    overflow: hidden;
  }
  .card {
    position: absolute;
    left: 207px;
    top: 213px;
    width: 786px;
    height: 228px;
    display: flex;
  }
  .card-back {
    width: 393px;
    height: 100%;
    background: var(--card-black);
    display: flex;
    align-items: center;
    justify-content: center;
  }
  .brand-badge {
    width: 142px;
    height: 142px;
    border-radius: 50%;
    background: var(--card-gold);
    display: flex;
    align-items: center;
    justify-content: center;
    margin-top: -2px;
  }
  .brand-name {
    font-family: "Open Sans", sans-serif;
    font-style: italic;
    font-weight: 400;
    font-size: 11px;
    color: var(--ink-dark);
    white-space: nowrap;
  }
  .card-front {
    position: relative;
    width: 393px;
    height: 100%;
    background: var(--card-gold);
    overflow: hidden;
  }
  .name {
    position: absolute;
    left: 62px;
    top: 80px;
    margin: 0;
    font-family: "Pinyon Script", cursive;
    font-weight: 400;
    font-size: 42px;
    line-height: 1;
    color: var(--ink-white);
    white-space: nowrap;
  }
  .role {
    position: absolute;
    left: 70px;
    top: 133px;
    margin: 0;
    font-family: "Open Sans", sans-serif;
    font-style: italic;
    font-weight: 600;
    font-size: 8.5px;
    color: var(--ink-dark);
    white-space: nowrap;
  }
  .rule {
    position: absolute;
    left: 188px;
    top: 146px;
    width: 132px;
    border-top: 1px dotted rgba(255,255,255,0.8);
  }
  .contact {
    position: absolute;
    left: 190px;
    top: 151px;
    margin: 0;
    font-family: "Open Sans", sans-serif;
    font-style: italic;
    font-weight: 400;
    font-size: 9.5px;
    line-height: 15px;
    color: var(--ink-dark);
  }
</style>
</head>
<body>
  <div class="canvas">
    <div class="card">
      <div class="card-back">
        <div class="brand-badge">
          <span class="brand-name">Rosalind Parfrey</span>
        </div>
      </div>
      <div class="card-front">
        <h1 class="name">Rosalind Parfrey</h1>
        <p class="role">Stylist or Wardrobe Stylist</p>
        <div class="rule"></div>
        <p class="contact">rosaparfrey@mailbox-example.co.nz<br>0218467193</p>
      </div>
    </div>
  </div>
</body>
</html>
```